Business Card Design Project for a Restaurant/Wine Bar

New, fresh business card design for Brevenna Wine Bar & Restaurant, Bandon, Oregon. We are an established restaurant on the Oregon coast featuring "Italian coastal cuisine."

"Brevenna" means bay leaf in Italian. We aren't sure if we would like our logo on the card or not, but if you have something interesting that uses it, then please do so. The basic information is essential - full restaurant name, address, phone and website (do not use www). The font on our menu and wine list may give you some sort of an idea of our style.

One-sided card needed as we often use the backside to write down various types of info for customers.
Updates

After seeing a few submissions, we would like to see what designers can come up with-using the logo, just the leaf, or none at all. Sky is the limit as long as our full restaurant name, address, phone and website (please leave out www) are there. Please contact us if questions!

I appreciate all of your designs! Our deadline is next week, but I will continue to give feedback on designs as I can. This is our busiest season, so my co-owner/chef/husband, won't have time to look at the designs for awhile. When he does, we can make our decision.

cheers,
Maren

Target Market(s)

Fine dining/wine crowd. Would like something simple and elegant, but not pretentious or stuffy. Brevenna means bay laurel (bay leaf) in Italian (please see our logo).

Industry/Entity Type

Restaurant

Requirements
Must have
• Full Name of Restaurant: Brevenna Wine Bar & Restaurant
Address: 812 4th Ave NW, Bandon, Oregon 97411
Phone: 541.555.0172
website: brevennawinebar.example (do not use www)
Should not have
• Loud colors.

```html
<!DOCTYPE html>
<html lang="en">
<head>
<meta charset="utf-8">
<title>Brevenna Wine Bar &amp; Restaurant – Business Card</title>
<link rel="stylesheet" href="https://fonts.googleapis.com/css2?family=Source+Sans+3:wght@400&family=Tinos:wght@400;700&display=swap">
<style>
  :root {
    --canvas: #e9e7e4;
    --card: #ffffff;
    --charcoal: #3f3e43;
    --tan: #a27b50;
    --ink: #2a2a2a;
    --text-grey: #4a4a4a;
    --rule: #c9c9c9;
    --faint: #dcdcdc;
  }
  html, body {
    margin: 0;
    padding: 0;
    width: 1200px;
    height: 966px;
    overflow: hidden;
    background: var(--canvas);
  }
  .sheet {
    position: relative;
    width: 1200px;
    height: 966px;
  }
  .card {
    position: absolute;
    left: 250px;
    width: 700px;
    height: 400px;
    border-radius: 26px;
    background: var(--card);
    overflow: hidden;
    box-shadow: 0 6px 18px rgba(0,0,0,0.18);
  }
  .card--front { top: 50px; }
  .card--back { top: 516px; }
  .card svg { display: block; }

  .brand-name {
    font-family: "Tinos", "Times New Roman", serif;
    font-weight: 700;
    font-size: 64px;
    fill: var(--ink);
  }
  .contact {
    font-family: "Source Sans 3", "Myriad Pro", sans-serif;
    font-size: 19px;
    fill: var(--text-grey);
  }
  .band-title {
    font-family: "Tinos", "Times New Roman", serif;
    font-size: 32px;
    fill: #ffffff;
  }
  .band { fill: var(--charcoal); }
  .swoosh { fill: var(--tan); }
  .icon-tan { fill: none; stroke: var(--tan); stroke-width: 1.6; }
  .icon-grey { fill: none; stroke: #777; stroke-width: 1.4; }

  .note-line { stroke: var(--rule); stroke-width: 1.2; }
  .brand-name--faint {
    font-family: "Tinos", "Times New Roman", serif;
    font-weight: 700;
    font-size: 84px;
    fill: var(--faint);
  }
</style>
</head>
<body>
<main class="sheet">

  <section class="card card--front" aria-label="Card front">
    <svg width="700" height="400" viewBox="0 0 700 400">
      <text class="brand-name" x="62" y="140">Brevenna</text>

      <path class="swoosh" d="M330 322 C500 305 645 230 700 58 L700 112 C655 230 520 312 330 322 Z"/>
      <path class="band" d="M0 338 C170 300 390 345 560 282 C640 250 685 190 700 130 L700 400 L0 400 Z"/>

      <g class="contact-block">
        <circle class="icon-tan" cx="73" cy="254" r="8"/>
        <path class="icon-tan" d="M70 249 q-2 5 3 10 l3 -2"/>
        <text class="contact" x="86" y="261">541.555.0172</text>
        <circle class="icon-grey" cx="228" cy="254" r="8"/>
        <ellipse class="icon-grey" cx="228" cy="254" rx="3.5" ry="8"/>
        <line class="icon-grey" x1="220" y1="254" x2="236" y2="254"/>
        <text class="contact" x="241" y="261">brevennawinebar.example</text>
        <text class="contact" x="64" y="294">812 4th Ave NW, Bandon, Oregon 97411</text>
      </g>

      <text class="band-title" x="48" y="386" transform="rotate(-6 48 386)">Brevenna Wine Bar &amp; Restaurant</text>
    </svg>
  </section>

  <section class="card card--back" aria-label="Card back for notes">
    <svg width="700" height="400" viewBox="0 0 700 400">
      <text class="brand-name--faint" x="350" y="228" text-anchor="middle">Brevenna</text>
      <g class="note-lines">
        <line class="note-line" x1="40" y1="48" x2="660" y2="48"/>
        <line class="note-line" x1="40" y1="82" x2="660" y2="82"/>
        <line class="note-line" x1="40" y1="116" x2="660" y2="116"/>
        <line class="note-line" x1="40" y1="150" x2="660" y2="150"/>
        <line class="note-line" x1="40" y1="184" x2="660" y2="184"/>
        <line class="note-line" x1="40" y1="218" x2="660" y2="218"/>
        <line class="note-line" x1="40" y1="252" x2="660" y2="252"/>
        <line class="note-line" x1="40" y1="286" x2="660" y2="286"/>
        <line class="note-line" x1="40" y1="320" x2="660" y2="320"/>
        <line class="note-line" x1="40" y1="354" x2="660" y2="354"/>
      </g>
    </svg>
  </section>

</main>
</body>
</html>
```